Web design for financial services

A modern web design of financial services (brokerage firm)
Req.s and technology tags :
- Very mobile friendly.
- One paged with some inner pages.
- Animated sticky header .
- Member login area for e-trade.
- Support RTL language.
- HTML & CSS.

The logo will be Home link
• MPTR :
WHO WE ARE
Content :
i) Board of Directors
ii) Mission Statement
iii) Corporate Values
iv) Regulations
• Financial Services :
WHAT WE DO
Content:
i) Electronic trading
ii) Trading desk
iii) Institutional
iv) Investors Education
• News
• Market Tools
• Forms---- opens new page
• Careers---- opens new page
• Contact Us----opens new page

The website is :
http://www.mptr-doha-example.com/

The logo need some changes to be more modern and impressively , but with keeping same structure .

Some related websites :
https://www.lv-bourse.example/

financial market

Financial Service

Coded - Design and coding required

2 page

• same fonts of http://www.kwdholdings.example/

• - Very mobile friendly.
• - One paged with some inner pages.
• - Animated sticky header .
• - Member login area for e-trade.
• - Support RTL language.
• - HTML & CSS.
• Slider , some Qatari theme,
• i like the video inside the home page
• ex :http://www.kwdholdings.example/

```html
<!DOCTYPE html>
<html lang="en">
<head>
<meta charset="utf-8">
<title>MPTR – Contact Us</title>
<link rel="stylesheet" href="https://fonts.googleapis.com/css2?family=Open+Sans:ital,wght@0,400;0,600;0,700;0,800;1,400&display=swap">
<style>
:root{
  --brand:#8b1a1a;
  --brand-dark:#6e1212;
  --ink:#111111;
  --text:#222222;
  --muted:#555555;
  --field:#d9d9d9;
  --white:#ffffff;
  --black:#000000;
}
*{box-sizing:border-box;margin:0;padding:0}
html,body{width:1200px;height:2635px;overflow:hidden;background:var(--white)}
body{position:relative;font-family:"Open Sans",sans-serif;color:var(--text)}
.abs{position:absolute}

/* header */
.site-header{left:0;top:0;width:1200px;height:120px;background:var(--white);box-shadow:0 2px 6px rgba(0,0,0,.08);z-index:5}
.brand{left:79px;top:38px;display:flex;align-items:center;gap:14px}
.brand-mark{width:46px;height:46px;border-radius:50%;background:var(--brand)}
.brand-name{font-weight:800;font-size:38px;color:var(--ink);letter-spacing:1px}
.etrade{left:926px;top:26px;width:102px;height:27px;background:var(--brand);color:var(--white);font-size:10.5px;font-weight:700;display:flex;align-items:center;justify-content:center;border-radius:3px}
.lang{left:1037px;top:26px;width:87px;height:27px;border:1px solid #999;font-size:10px;font-weight:600;display:flex;align-items:center;justify-content:center;gap:6px;border-radius:3px}
.lang i{width:12px;height:8px;background:#2a3f8f;display:inline-block}
.main-nav{top:81px;left:0;width:1200px;height:20px;font-size:12px;font-weight:700;color:var(--ink)}
.main-nav span{position:absolute;white-space:nowrap}
.main-nav .active{color:var(--brand)}

/* hero */
.hero{left:0;top:120px;width:1200px;height:548px;background:linear-gradient(120deg,#2b2d2f 0%,#4a4744 35%,#6a6662 55%,#3a3836 80%,#23201e 100%)}
.hero-title{left:0;top:300px;width:1200px;text-align:center;color:var(--white);font-weight:700;font-size:64px;letter-spacing:1px}
.cut{left:0;width:1200px}

/* sections */
.section-title{font-weight:700;font-size:27px;color:var(--ink);letter-spacing:.3px}
.intro{font-style:italic;font-size:14.5px;line-height:24px;color:var(--text);width:600px}
.info-col h3{font-size:16px;font-weight:600;color:var(--brand);margin-bottom:10px}
.info-col p{font-size:12px;line-height:27px;color:var(--text)}

.map{left:0;top:1119px;width:1200px;height:545px;background:linear-gradient(160deg,#e6e6e6,#d4d4d4 50%,#e2e2e2)}

/* form */
.field{border:1px solid var(--field);background:var(--white);font-size:11px;padding:9px 8px;color:var(--text)}
.submit{left:162px;top:1950px;width:91px;height:39px;background:var(--brand);color:var(--white);font-weight:700;font-size:13px;display:flex;align-items:center;justify-content:center}

.skyline{left:0;top:2056px;width:1200px;height:325px;background:linear-gradient(180deg,rgba(139,26,26,0) 0%,rgba(139,26,26,.35) 30%,#a5524e 65%,var(--brand-dark) 100%)}

/* footer */
.site-footer{left:0;top:2381px;width:1200px;height:254px;background:var(--black);color:var(--white)}
.footer-brand{left:0;top:48px;width:1200px;display:flex;justify-content:center;align-items:center;gap:10px}
.footer-brand .brand-mark{width:34px;height:34px;background:var(--white)}
.footer-brand .brand-name{color:var(--white);font-size:28px}
.footer-nav{left:0;top:127px;width:1200px;text-align:center;font-size:12.5px;font-weight:700;letter-spacing:.3px}
.footer-nav b{font-weight:400;margin:0 13px}
.copyright{left:0;top:159px;width:1200px;text-align:center;font-size:10px;color:#bbb}
.social{left:0;top:190px;width:1200px;display:flex;justify-content:center;gap:10px}
.social i{width:28px;height:28px;border:1.5px solid var(--white);border-radius:50%}
</style>
</head>
<body>

<header class="site-header abs">
  <a class="brand abs"><span class="brand-mark"></span><span class="brand-name">MPTR</span></a>
  <div class="etrade abs">MPTR E-TRADE</div>
  <div class="lang abs"><i></i>ENGLISH ⌄</div>
  <nav class="main-nav abs">
    <span style="left:507px">MPTR</span>
    <span style="left:567px">FINANCIAL SERVICE</span>
    <span style="left:710px">NEWS</span>
    <span style="left:778px">MARKET TOOL</span>
    <span style="left:894px">FORMS</span>
    <span style="left:968px">CAREERS</span>
    <span class="active" style="left:1052px">CONTACT US</span>
  </nav>
</header>

<section class="hero abs" role="img" aria-label="Photo of a person reviewing printed financial charts beside a laptop on a desk"></section>
<h1 class="hero-title abs">GET IN TOUCH</h1>
<svg class="cut abs" style="top:520px" width="1200" height="150" viewBox="0 0 1200 150"><polygon points="0,74 369,2 1200,148 1200,150 0,150" fill="#fff"/></svg>

<h2 class="section-title abs" style="left:160px;top:676px">CONTACT US</h2>
<p class="intro abs" style="left:430px;top:664px">Sed ut perspiciatis unde omnis iste natus error sit voluptatem accusantium doloremque laudantium, totam rem aperiam, eaque ipsa quae ab illo inventore veritatis et quasi architecto beatae vitae dicta suaque ipsa quae ab illo inventore veritatis.</p>

<div class="info-col abs" style="left:160px;top:814px">
  <h3>Bourse Hall Branch</h3>
  <p>First Floor, Falcon Tower, Corniche in<br>front of Pearl Plaza<br>Tel: +974 40001234<br>Fax: +974 40005678<br>Email: info@mptr-doha-example.com<br>Compliance Mail<br>complaints@mptr-doha-example.com<br>Recruitment<br>recruitment@mptr-doha-example.com</p>
</div>
<div class="info-col abs" style="left:430px;top:814px">
  <h3>Al Noor Complex</h3>
  <p>First Floor, Garden Junction<br>Tel: +974 40009012<br>Fax: +974 40003456<br>Email: info@mptr-doha-example.com<br>Compliance Mail<br>complaints@mptr-doha-example.com<br>Recruitment</p>
</div>
<div class="info-col abs" style="left:701px;top:814px">
  <h3>Office Hours</h3>
  <p>Sunday - Thursday<br>From 8:00 AM - 3:00 PM<br>Friday &nbsp;And Saturday<br>are officail holiday</p>
</div>
<div class="info-col abs" style="left:910px;top:814px">
  <h3>Trading Hours</h3>
  <p>Sunday - Thursday<br>Pre-Open: 9:00 AM<br>Market Open: 9:30 AM<br>Pre-Close: 1:00 PM<br>Market Close: 1:15 PM</p>
</div>

<div class="map abs" role="img" aria-label="Street map showing the office location"></div>
<svg class="abs" style="left:580px;top:1282px" width="36" height="50" viewBox="0 0 36 50"><path d="M18 0C8 0 0 8 0 18c0 13 18 32 18 32s18-19 18-32C36 8 28 0 18 0z" fill="#8b1a1a"/><circle cx="18" cy="17" r="6" fill="#fff"/></svg>
<svg class="cut abs" style="top:1490px" width="1200" height="175" viewBox="0 0 1200 175"><polygon points="0,86 369,6 1200,170 1200,175 0,175" fill="#fff"/></svg>

<h2 class="section-title abs" style="left:160px;top:1681px">CONTACT FORM</h2>
<p class="intro abs" style="left:430px;top:1669px">Sed ut perspiciatis unde omnis iste natus error sit voluptatem accusantium doloremque laudantium, totam rem aperiam, eaque ipsa quae ab illo inventore veritatis et quasi architecto beatae vitae dicta suaque ipsa quae ab illo inventore veritatis.</p>

<div class="field abs" style="left:160px;top:1796px;width:425px;height:35px">Name:</div>
<div class="field abs" style="left:160px;top:1847px;width:425px;height:35px">Phone:</div>
<div class="field abs" style="left:160px;top:1892px;width:425px;height:35px">Email:</div>
<div class="field abs" style="left:611px;top:1796px;width:426px;height:133px">Message:</div>
<div class="submit abs">SUBMIT</div>

<div class="skyline abs" role="img" aria-label="Illustrated skyline of the city's towers in red tones"></div>

<footer class="site-footer abs">
  <div class="footer-brand abs"><span class="brand-mark"></span><span class="brand-name">MPTR</span></div>
  <nav class="footer-nav abs">MPTR<b>|</b>FINACIAL SERVICE<b>|</b>NEWS<b>|</b>MARKET TOOL<b>|</b>CAREERS<b>|</b>CONTACT US</nav>
  <p class="copyright abs">©2017. All Rights Reserved | MPTR Doha | Copyright, Legal and Privacy Statement,Disclaimers and Legal Information</p>
  <div class="social abs"><i></i><i></i><i></i><i></i><i></i></div>
</footer>

</body>
</html>
```